Dorla's Cleaners new delivery postcard

We need to advertise for our new pick up and delivery dry cleaning/laundry service.
Mens Business Shirts $2.00
Pants $4.50
Skirts $5.00
Dry Clean Shirt/Blouse $5.00
Dress $9.00
2 Piece Suits $9.00
Updates
We would like to use a 5x7 size postcard, printed on both sides. We would like to add a discount to the card for 25% off of their first order, with the flyer.
We are a famly run dry cleaners. My name is Rosalind Tupper and my cell # is 614-302-7781. We are trying to expand our business to include free pick and delivery.
If possible can you use the logo I sent some where on the postcard? The phone # for the store is 614-295-3064.
Reason: Still need to get partners approval.

```html
<!DOCTYPE html>
<html lang="en">
<head>
<meta charset="utf-8">
<title>Dorla's Cleaners – Delivery Postcard</title>
<link rel="stylesheet" href="https://fonts.googleapis.com/css2?family=Titan+One&family=Fredoka:wght@500;600;700&family=Montserrat:wght@400;500&display=swap">
<style>
  :root {
    --page: #ece9e4;
    --sky-top: #e9f5fc;
    --sky-mid: #9fd2f1;
    --sky-deep: #2f8fd8;
    --panel-blue: #2c86cf;
    --navy: #1d4f9c;
    --brand-blue: #1a8fd0;
    --orange: #f26f21;
    --green: #6cbf3a;
    --yellow: #f6b51f;
    --white: #ffffff;
    --band: #f2f4f6;
    --right-blue: #2a86cc;
  }
  * { margin: 0; padding: 0; box-sizing: border-box; }
  html, body { width: 1200px; height: 900px; overflow: hidden; background: var(--page); }
  .canvas { position: relative; width: 1200px; height: 900px; }

  .postcard {
    position: absolute; width: 560px; height: 400px; overflow: hidden;
    background: var(--band);
    box-shadow: 0 8px 24px rgba(0,0,0,.18);
  }
  .postcard--front { left: 40px; top: 60px; }
  .postcard--back { left: 600px; top: 400px; }

  .water {
    position: absolute; left: 0; top: 0; width: 100%;
    background: linear-gradient(180deg, var(--sky-top) 0%, var(--sky-mid) 55%, var(--sky-deep) 100%);
  }
  .postcard--front .water { height: 335px; }
  .postcard--back .water { height: 355px; }

  .brand { position: absolute; display: flex; align-items: center; gap: 10px; }
  .brand__mark { width: 42px; height: 42px; background: var(--navy); }
  .brand__name {
    font-family: "Titan One", sans-serif; font-size: 29px; color: var(--brand-blue);
    text-transform: uppercase; letter-spacing: .5px;
  }
  .postcard--front .brand { left: 22px; top: 14px; }
  .postcard--back .brand { left: 40px; top: 24px; }
  .postcard--back .brand__name { font-size: 28px; }

  .price-list {
    position: absolute; left: 16px; top: 100px; width: 262px; padding: 16px 22px 10px 22px;
    background: var(--panel-blue); border-radius: 0 10px 10px 0;
    font-family: "Montserrat", sans-serif; font-size: 14.5px; color: var(--white);
    list-style: none;
  }
  .price-list li { display: flex; justify-content: space-between; line-height: 25px; }

  .offer {
    position: absolute; left: 305px; top: 65px; width: 215px; height: 215px; border-radius: 50%;
    background: radial-gradient(circle at 45% 40%, #ffffff 0%, #eaf6fd 55%, #a9d8f4 100%);
    border: 3px solid rgba(255,255,255,.85);
    display: flex; flex-direction: column; align-items: center; justify-content: center;
    font-family: "Fredoka", sans-serif; text-align: center; line-height: 1;
  }
  .offer__value { font-size: 66px; font-weight: 600; color: var(--orange); }
  .offer__label { font-size: 38px; font-weight: 500; color: var(--brand-blue); }
  .offer__note { font-size: 22px; font-weight: 500; color: var(--green); }

  .cta { position: absolute; font-family: "Fredoka", sans-serif; font-weight: 700; }
  .cta__prompt { display: block; color: var(--white); font-size: 26px; line-height: 1; }
  .cta__phone { display: block; color: var(--navy); font-size: 42px; line-height: 1.1; letter-spacing: .5px; }
  .postcard--front .cta { left: 46px; top: 297px; }
  .postcard--back .cta { left: 48px; top: 230px; }
  .postcard--back .cta__prompt { color: var(--white); }

  .back-shape { position: absolute; left: 0; top: 0; width: 560px; height: 355px; }
  .services {
    position: absolute; left: 110px; top: 64px; width: 330px; text-align: center;
    font-family: "Fredoka", sans-serif; font-weight: 600; font-size: 16px; line-height: 19px;
    color: var(--yellow);
  }
  .headline {
    position: absolute; left: 70px; top: 145px;
    font-family: "Fredoka", sans-serif; font-weight: 700; font-size: 31px; color: var(--navy);
  }
  .headline__lead { color: var(--green); }
</style>
</head>
<body>
<main class="canvas">

  <section class="postcard postcard--front" aria-label="Postcard front">
    <div class="water"></div>
    <div class="brand">
      <span class="brand__mark"></span>
      <span class="brand__name">Dorla's Cleaners</span>
    </div>
    <ul class="price-list">
      <li><span>Mens Business Shirts</span><span>$2.00</span></li>
      <li><span>Pants</span><span>$4.50</span></li>
      <li><span>Skirts</span><span>$5.00</span></li>
      <li><span>Dry Clean Shirt/Blouse</span><span>$5.00</span></li>
      <li><span>Dress</span><span>$9.00</span></li>
      <li><span>2 Piece Suits</span><span>$9.00</span></li>
    </ul>
    <div class="offer">
      <span class="offer__value">25%</span>
      <span class="offer__label">discount</span>
      <span class="offer__note">on first order</span>
    </div>
    <div class="cta">
      <span class="cta__prompt">Call NOW</span>
      <span class="cta__phone">614-295-3064</span>
    </div>
  </section>

  <section class="postcard postcard--back" aria-label="Postcard back">
    <div class="water"></div>
    <svg class="back-shape" viewBox="0 0 560 355" aria-hidden="true">
      <rect x="380" y="0" width="180" height="355" fill="var(--right-blue)"/>
      <path d="M0 0 H470 C520 80 520 250 420 305 C330 345 150 345 0 335 Z" fill="var(--green)"/>
      <path d="M0 0 H458 C505 80 505 240 412 294 C325 332 150 332 0 324 Z" fill="rgba(255,255,255,.92)"/>
      <path d="M0 180 C120 170 300 200 470 170 C450 250 420 290 412 294 C325 332 150 332 0 324 Z" fill="rgba(120,190,236,.7)"/>
    </svg>
    <div class="brand">
      <span class="brand__mark"></span>
      <span class="brand__name">Dorla's Cleaners</span>
    </div>
    <p class="services">•Dry cleaning •Shirt laundry •Alterations<br>•Wedding dresses •Storage</p>
    <h2 class="headline"><span class="headline__lead">Free</span> Delivery &amp; Pick up</h2>
    <div class="cta">
      <span class="cta__prompt">Call NOW</span>
      <span class="cta__phone">614-295-3064</span>
    </div>
  </section>

</main>
</body>
</html>
```